Update informational website

I need a new modern site design for my website.

Here is the site: http://q.zq/kpTr

Here is a theme I liked: http://q.zq/kpTm

I am looking for something with clean lines and an exciting designs and graphics, please use images from brindlecove.com and track the images used so I can buy them if I like the design.

I just need the homepage and one interior page designed.

Colors
Bright Green #6ed30d
Dark Text #222
Lighter Text #444

Number of Pages Required

2 page

Font styles to use
Sans Serif

Requirements
Must have
• Clean, good spacing, responsive design, high resolution design

```html
<!DOCTYPE html>
<html lang="en">
<head>
<meta charset="utf-8">
<title>Mesa Tint — Window Tint</title>
<link href="https://fonts.googleapis.com/css2?family=Raleway:wght@500;700;800&family=PT+Sans:wght@400;700&display=swap" rel="stylesheet">
<style>
:root{
  --green:#6ed30d;
  --dark:#222;
  --text:#444;
  --muted:#777;
  --night:#14171a;
  --white:#fff;
  --paper:#f7f7f7;
}
*{margin:0;padding:0;box-sizing:border-box}
html,body{width:1200px;height:2579px;overflow:hidden}
body{position:relative;background:var(--white);font-family:"PT Sans",Arial,sans-serif;color:var(--text)}
.abs{position:absolute}
.heading{font-family:"Raleway",Arial,sans-serif;font-weight:800;color:var(--dark);text-align:center;text-transform:uppercase}

/* hero */
.hero{left:0;top:0;width:1200px;height:585px;clip-path:polygon(0 0,1200px 0,1200px 537px,585px 585px,0 537px);
  background:linear-gradient(100deg,#6c6358 0%,#8c7d69 30%,#5b5149 55%,#3a3532 80%,#2b2827 100%)}
.hero-car{left:560px;top:130px;width:560px;height:330px;border-radius:40% 40% 18% 18%;
  background:radial-gradient(ellipse at 50% 45%,#b8242a 0%,#8d1a1f 45%,rgba(60,20,20,.0) 75%)}
.topbar{left:0;top:0;width:1200px;height:40px;background:rgba(0,0,0,.35);border-bottom:1px solid rgba(255,255,255,.15);
  font-size:11px;color:#e6e6e6;letter-spacing:.3px}
.topbar .item{top:13px;display:flex;align-items:center;gap:7px}
.social{top:13px;left:1005px;display:flex;gap:12px;align-items:center}
.social span{width:9px;height:9px;border-radius:50%;background:#cfcfcf}
.logo{left:134px;top:72px;display:flex;align-items:center;gap:8px;font-family:"Raleway",sans-serif;font-weight:800;font-size:26px;color:var(--green)}
.logo i{width:14px;height:14px;background:var(--green);display:block}
.nav{top:82px;left:470px;display:flex;gap:0;font-family:"Raleway",sans-serif;font-weight:700;font-size:12px;color:var(--white);text-transform:uppercase}
.nav a{color:inherit;text-decoration:none;position:absolute;white-space:nowrap}
.nav a.active{color:var(--green)}
.hero-title{left:133px;top:232px;font-family:"Raleway",sans-serif;font-weight:800;font-size:62px;color:var(--white)}
.hero-sub{left:156px;top:310px;width:370px;font-size:16px;line-height:27px;color:#f0f0f0}
.btn{left:244px;top:387px;width:138px;height:40px;background:var(--green);color:var(--white);font-family:"Raleway",sans-serif;font-weight:700;font-size:12px;display:flex;align-items:center;justify-content:center;text-transform:uppercase}
.dots{left:557px;top:531px;display:flex;gap:10px}
.dots span{width:14px;height:14px;border-radius:50%;border:2px solid var(--white)}
.dots span.on{background:var(--green);border-color:var(--green)}

/* about */
.about-bg{left:0;top:540px;width:1200px;height:483px;background:var(--paper);z-index:-1}
.about-car{left:225px;top:820px;width:760px;height:195px;border-radius:45% 45% 20% 20%;
  background:radial-gradient(ellipse at 50% 55%,#d9dde1 0%,#e6e9ec 45%,rgba(247,247,247,0) 75%)}
.about-kicker{left:0;top:675px;width:1200px;font-size:17px;font-weight:700}
.about-title{left:0;top:700px;width:1200px;font-size:31px}
.about-copy{left:172px;top:750px;width:856px;font-size:12px;line-height:23px;color:var(--text);text-align:center}
.about-copy p{margin-bottom:12px}

/* services */
.services{left:0;top:1023px;width:1200px;height:451px;background:linear-gradient(180deg,#1d2125 0%,#2c3034 40%,#16191c 100%)}
.tri{top:994px}
.services-title{left:0;top:1100px;width:1200px;font-size:28px;color:var(--white);font-weight:700}
.cards{left:132px;top:1161px;width:936px;height:225px;display:flex;background:var(--white)}
.card{flex:1;text-align:center;border-left:1px solid #ddd;padding-top:45px}
.card:first-child{border-left:none}
.card.featured{background:var(--green)}
.card svg{height:62px;display:block;margin:0 auto}
.card h3{margin-top:24px;font-family:"Raleway",sans-serif;font-weight:700;font-size:13px;color:var(--dark);text-transform:uppercase}
.card p{margin-top:9px;font-size:11px;color:var(--text)}
.card .more{margin-top:9px;font-family:"Raleway",sans-serif;font-weight:700;font-size:10px;color:var(--green);text-transform:uppercase}
.card.featured h3,.card.featured p,.card.featured .more{color:var(--white)}

/* film */
.film-title{left:0;top:1545px;width:1200px;font-size:28px}
.film-copy{left:220px;top:1585px;width:760px;text-align:center;font-size:12px;line-height:20px}
.tile{top:1651px;height:224px;display:flex;align-items:flex-end;justify-content:center;padding-bottom:14px;
  font-family:"Raleway",sans-serif;font-weight:700;font-size:14px;color:var(--white);text-transform:uppercase}
.tile.commercial{left:132px;width:467px;background:linear-gradient(180deg,#3f7fc4 0%,#5c8fb8 45%,#1d2c3c 100%)}
.tile.auto{left:605px;width:228px;background:radial-gradient(ellipse at 50% 55%,#cfd2d4 0%,#5a5c5e 30%,#111 70%)}
.tile.residential{left:839px;width:229px;background:linear-gradient(180deg,#9a9c94 0%,#bfc0b8 50%,#4f5a3f 100%)}

/* gallery */
.gallery{left:0;top:1952px;width:1200px;height:413px;background:linear-gradient(180deg,#3a3e40 0%,#25282a 50%,#3b3a34 100%)}
.gallery-title{left:0;top:2033px;width:1200px;font-size:26px;color:var(--white);font-weight:700}
.gallery-sub{left:0;top:2078px;width:1200px;text-align:center;font-size:12px;color:#e0e0e0}
.shot{top:2126px;height:148px}
.shot.a{left:132px;width:240px;clip-path:polygon(0 0,100% 0,97% 100%,0 100%);background:linear-gradient(180deg,#b9c9d6,#6d8aa3)}
.shot.b{left:366px;width:240px;clip-path:polygon(3% 0,100% 0,97% 100%,0 100%);background:linear-gradient(160deg,#7aa0b7 0%,#c6272c 55%,#5a4a3c 100%)}
.shot.c{left:600px;width:240px;clip-path:polygon(3% 0,100% 0,97% 100%,0 100%);background:linear-gradient(180deg,#8ea3b5 0%,#dfe2e4 55%,#7c7a72 100%)}
.shot.d{left:834px;width:234px;clip-path:polygon(3% 0,100% 0,100% 100%,0 100%);background:linear-gradient(180deg,#a8bccc 0%,#c3283a 55%,#9d907c 100%)}
.rule{left:0;top:2365px;width:1200px;height:5px;background:var(--green)}

/* footer */
.contact{top:2403px;display:flex;align-items:center;gap:12px;font-size:13px;color:var(--muted);line-height:20px}
.contact .ring{width:40px;height:40px;border-radius:50%;border:1px solid #cfcfcf;display:flex;align-items:center;justify-content:center;flex:none}
.footnav{top:2478px;left:0;width:1200px;display:flex;justify-content:center;gap:30px;font-family:"Raleway",sans-serif;font-weight:500;font-size:12px;color:var(--dark);text-transform:uppercase}
.footnav .sep{color:#999}
.divider{left:0;top:2523px;width:1200px;height:1px;background:#e2e2e2}
.copyright{left:0;top:2543px;width:1200px;text-align:center;font-size:12px;color:var(--muted)}
</style>
</head>
<body>

<section class="abs hero" role="img" aria-label="Red sports sedan driving on a blurred road at sunset">
  <div class="abs hero-car"></div>
</section>

<header class="abs topbar">
  <div class="abs item" style="left:131px">
    <svg width="8" height="12" viewBox="0 0 8 12"><rect x=".5" y=".5" width="7" height="11" rx="1.2" fill="none" stroke="#ddd"/></svg>
    CALL US : 480.555.0142
  </div>
  <div class="abs item" style="left:270px">
    <svg width="11" height="8" viewBox="0 0 11 8"><rect width="11" height="8" fill="#ddd"/><path d="M0 0l5.5 4.5L11 0" stroke="#555" fill="none"/></svg>
    EMAIL US : info@mesatint.com
  </div>
  <div class="abs item" style="left:860px">FOLLOW US :</div>
  <div class="abs social"><span></span><span></span><span></span><span></span><span></span></div>
</header>

<div class="abs logo"><i></i>Mesa Tint</div>
<nav class="abs nav">
  <a class="active" style="left:0">Home</a>
  <a style="left:88px">Window Film Services</a>
  <a style="left:275px">Film</a>
  <a style="left:352px">About</a>
  <a style="left:443px">Gallery</a>
  <a style="left:543px">Contact</a>
</nav>

<h1 class="abs hero-title">WindowTint</h1>
<p class="abs hero-sub">Aliquip ex ea commodo consequat. Duis aute irure dolor reprehenderit...</p>
<a class="abs btn">Learn More Info</a>
<div class="abs dots"><span class="on"></span><span></span><span></span><span></span></div>

<section>
  <div class="abs about-bg"></div>
  <div class="abs about-car" role="img" aria-label="Faded white sports car"></div>
  <h2 class="abs heading about-kicker">About</h2>
  <h2 class="abs heading about-title">MESATINT</h2>
  <div class="abs about-copy">
    <p>Mesa Tinting is not just another tint shop. We specialize in one thing and one thing only; Window Tinting. We offer Residential, Commercial and Automotive tinting services. Our philosophy is simple; do things right the first time! After 18 years we have learned that there is no such thing as a small job.</p>
    <p>Whether you need your personal car tinted, your new home protected or a complete face lift on your 10 story building, we believe that quality installation, attention to detail and customer service are the cornerstone's of a job well done.</p>
    <p>As a player in the Phoenix tint market for over twenty years, we have had the privilege to work with two of the best Window Film Manufacturers in the world. The knowledge and experience we have obtained in the last two decades makes us one of the most experienced operations in the valley. We know how the window film industry works, especially when it comes to factory warranties, installation guidelines and trade secrets.</p>
  </div>
</section>

<section>
  <div class="abs services" role="img" aria-label="Dark blurred car in a night setting"></div>
  <svg class="abs tri" style="left:0" width="130" height="94" viewBox="0 0 130 94"><polygon points="0,0 129,29 0,93" fill="var(--green)"/></svg>
  <svg class="abs tri" style="left:1070px" width="130" height="94" viewBox="0 0 130 94"><polygon points="130,0 1,29 130,93" fill="var(--green)"/></svg>
  <h2 class="abs heading services-title">Window Film Services</h2>
  <div class="abs cards">
    <div class="card featured">
      <svg viewBox="0 0 120 62" width="120"><path d="M8 44 Q6 34 20 31 L38 30 L52 18 Q58 14 70 14 L86 14 Q94 14 100 22 L106 30 Q114 32 114 40 L114 44 Z" fill="none" stroke="#fff" stroke-width="3"/><circle cx="32" cy="46" r="7" fill="var(--green)" stroke="#fff" stroke-width="3"/><circle cx="92" cy="46" r="7" fill="var(--green)" stroke="#fff" stroke-width="3"/></svg>
      <h3>Automotive Film</h3><p>Heat, infrared, and UV protection</p><div class="more">Read More ›</div>
    </div>
    <div class="card">
      <svg viewBox="0 0 70 62" width="70"><path d="M35 4 L66 28 L60 28 L60 58 L10 58 L10 28 L4 28 Z" fill="var(--green)"/><rect x="22" y="32" width="26" height="26" rx="13" fill="#fff"/><rect x="26" y="38" width="18" height="20" fill="var(--green)"/></svg>
      <h3>Commercial &amp; Residential</h3><p>Your Valley Commercial Film</p><div class="more">Read More ›</div>
    </div>
    <div class="card">
      <svg viewBox="0 0 80 62" width="80"><path d="M4 31 Q40 -6 76 31 Q40 68 4 31 Z" fill="var(--green)"/><circle cx="40" cy="31" r="14" fill="#fff"/><circle cx="40" cy="31" r="8" fill="var(--green)"/></svg>
      <h3>Clear Bra</h3><p>Protect Your Paint</p><div class="more">Read More ›</div>
    </div>
    <div class="card">
      <svg viewBox="0 0 66 66" width="62"><g fill="var(--green)"><circle cx="33" cy="33" r="22"/><rect x="28" y="2" width="10" height="12"/><rect x="28" y="52" width="10" height="12"/><rect x="2" y="28" width="12" height="10"/><rect x="52" y="28" width="12" height="10"/><rect x="28" y="2" width="10" height="12" transform="rotate(45 33 33)"/><rect x="28" y="52" width="10" height="12" transform="rotate(45 33 33)"/><rect x="2" y="28" width="12" height="10" transform="rotate(45 33 33)"/><rect x="52" y="28" width="12" height="10" transform="rotate(45 33 33)"/></g><circle cx="33" cy="33" r="9" fill="#fff"/></svg>
      <h3>Vehicle Wraps</h3><p>An easy solution to a boring car</p><div class="more">Read More ›</div>
    </div>
  </div>
</section>

<section>
  <h2 class="abs heading film-title">Film</h2>
  <p class="abs film-copy">Lorem ipsum dolor sit amet, consectetur adipiscing elit, sed do eiusmod tempor incididunt ut labore et dolore magna aliqua. Ut enim ad minim veniam, quis nostrud exercitation ullamco laboris nisi ut aliquip ex ea commodo consequat</p>
  <div class="abs tile commercial" role="img" aria-label="Glass office towers at dusk">Commercial Window Film</div>
  <div class="abs tile auto" role="img" aria-label="White coupe on a dark studio floor">Auto Window Film</div>
  <div class="abs tile residential" role="img" aria-label="House facade with a white framed window">Residential Window Film</div>
</section>

<section>
  <div class="abs gallery" role="img" aria-label="Dark SUV parked in a desert landscape"></div>
  <h2 class="abs heading gallery-title">Gallery</h2>
  <p class="abs gallery-sub">Nostrud exercitation ullamco laboris nisi ut aliquip ex ea commodo consequat</p>
  <div class="abs shot a" role="img" aria-label="Glass skyscrapers"></div>
  <div class="abs shot b" role="img" aria-label="Red supercar by palm trees"></div>
  <div class="abs shot c" role="img" aria-label="White sports car on a road"></div>
  <div class="abs shot d" role="img" aria-label="Red roadster on a coastal road"></div>
  <div class="abs rule"></div>
</section>

<footer>
  <div class="abs contact" style="left:287px">
    <span class="ring"><svg width="12" height="17" viewBox="0 0 12 17"><path d="M6 0a6 6 0 0 1 6 6c0 4.5-6 11-6 11S0 10.5 0 6a6 6 0 0 1 6-6z" fill="var(--green)"/><circle cx="6" cy="6" r="2.3" fill="#fff"/></svg></span>
    <span>4120 E. Palo Verde Ln. Suite B<br>Phoenix, Az. 85018</span>
  </div>
  <div class="abs contact" style="left:566px">
    <span class="ring"><svg width="15" height="15" viewBox="0 0 24 24"><path d="M6.6 10.8a15.1 15.1 0 0 0 6.6 6.6l2.2-2.2a1 1 0 0 1 1-.25 11.4 11.4 0 0 0 3.6.57 1 1 0 0 1 1 1V20a1 1 0 0 1-1 1A17 17 0 0 1 3 4a1 1 0 0 1 1-1h3.5a1 1 0 0 1 1 1c0 1.25.2 2.45.57 3.57a1 1 0 0 1-.25 1z" fill="var(--green)"/></svg></span>
    <span>480.555.0142</span>
  </div>
  <div class="abs contact" style="left:765px">
    <span class="ring"><svg width="16" height="12" viewBox="0 0 16 12"><rect width="16" height="12" rx="1" fill="var(--green)"/><path d="M0 1l8 6 8-6" stroke="#fff" stroke-width="1.5" fill="none"/></svg></span>
    <span>hello@mesatint.com</span>
  </div>
  <nav class="abs footnav">
    <span>Home</span><span class="sep">|</span><span>Window Film Services</span><span class="sep">|</span><span>Film</span><span class="sep">|</span><span>About</span><span class="sep">|</span><span>Gallery</span><span class="sep">|</span><span>Contact</span>
  </nav>
  <div class="abs divider"></div>
  <p class="abs copyright">Copyrights © 2017, mesatint.com. All rights reserved.</p>
</footer>

</body>
</html>
```